Sports Nutrition line needs new label look/feel

We need a new label design for "Volrex",our Sports Nutrition line of vitamins, nutraceuticals, protein powders, and performance endurance products. We would like to see two separate designs, one blue and one red, as these are the two colors we are torn between. The labels should have the look/feel of a sports or fitness label, bold coloring, lettering, and even some use of holographic foiling.
Brands we would be similar to those found on gymstackhub.com and strongpathmarket.com. Brands we like in particular are KTW and Velmora.

Target Market(s)

Fitness enthusiasts,athletes, health nuts..

Industry/Entity Type

Nutrition

Font styles to use
Sans Serif
Decorative
Script

Colors
ec1f27
0692cd
0355a3
3276b5
f04a50

Requirements
Must have
• -Fitness look/feel
• -bold colors (preferably red and blue)
• -use of icons (eye health, brain, health, etc.)
• -"Fit" in "VolREX" must stand out
• -use tagline "Powering Active Lives"
Nice to have
• -holographic foiling elements
• -try to incorporate a molecular element (like those shown in the example labels)
Should not have
• -Light, calming colors
• -difficult to read fonts

```html
<!DOCTYPE html>
<html lang="en">
<head>
<meta charset="utf-8">
<title>Volrex Grape Seed Extract Labels</title>
<link rel="stylesheet" href="https://fonts.googleapis.com/css2?family=Anton&family=Roboto+Condensed:ital,wght@0,400;0,700;1,400&display=swap">
<style>
  :root {
    --canvas-bg: #eef0f0;
    --silver-light: #f2f2f2;
    --silver-dark: #9a9ea3;
    --blue-deep: #0a3f7a;
    --blue-mid: #0355a3;
    --blue-bright: #0692cd;
    --blue-accent: #3276b5;
    --red-deep: #7d0d12;
    --red-mid: #b3141b;
    --red-bright: #ec1f27;
    --red-accent: #f04a50;
    --white: #ffffff;
    --icon-ring: #ffffff;
  }
  * { box-sizing: border-box; margin: 0; padding: 0; }
  html, body {
    width: 1200px; height: 1200px; overflow: hidden;
    background: var(--canvas-bg);
  }
  .canvas {
    position: relative; width: 1200px; height: 1200px;
    background: linear-gradient(180deg, #f4f6f6 0%, #e6e9ea 55%, #f1f3f3 100%);
  }
  .label {
    position: absolute; width: 302px; height: 312px;
    overflow: hidden;
    font-family: "Roboto Condensed", "Arial Narrow", sans-serif;
    color: var(--white);
  }
  .label--blue {
    --body-deep: var(--blue-deep);
    --body-mid: var(--blue-mid);
    --body-bright: var(--blue-bright);
    --accent: var(--blue-accent);
    --title-shadow: #062a52;
  }
  .label--red {
    --body-deep: var(--red-deep);
    --body-mid: var(--red-mid);
    --body-bright: var(--red-bright);
    --accent: var(--red-bright);
    --title-shadow: #4a0508;
  }
  .label__band {
    position: absolute; left: 0; right: 0; height: 8px;
    background: linear-gradient(180deg, var(--silver-light), var(--silver-dark) 60%, var(--silver-light));
  }
  .label__band--top { top: 0; }
  .label__band--bottom { bottom: 0; }
  .label__body {
    position: absolute; left: 0; right: 0; top: 8px; bottom: 8px;
    background:
      radial-gradient(ellipse at 30% 55%, var(--body-bright) 0%, transparent 60%),
      radial-gradient(ellipse at 85% 20%, var(--body-bright) 0%, transparent 45%),
      linear-gradient(160deg, var(--body-mid) 0%, var(--body-deep) 100%);
  }
  .brand {
    position: absolute; left: 120px; top: 46px;
    display: flex; align-items: center; gap: 8px;
  }
  .brand__dot {
    width: 18px; height: 18px; border-radius: 50%;
    background: var(--silver-light);
  }
  .brand__name {
    font-family: "Anton", "Impact", sans-serif;
    font-size: 36px; line-height: 1; color: var(--white);
  }
  .brand__tagline {
    position: absolute; left: 140px; top: 98px;
    font-size: 12px; color: #e6e9ee;
  }
  .product-title {
    position: absolute; left: 0; right: 0; top: 118px;
    text-align: center;
    font-family: "Anton", "Impact", sans-serif;
    font-size: 38px; line-height: 1; letter-spacing: -0.5px;
    color: var(--white);
    text-shadow: 2px 2px 0 var(--title-shadow);
  }
  .product-claim {
    position: absolute; left: 0; right: 0; top: 172px;
    text-align: center; font-style: italic;
    font-size: 14px; color: #f1f3f6;
  }
  .benefit-icons {
    position: absolute; left: 24px; top: 204px;
    display: flex; gap: 14px; list-style: none;
  }
  .benefit-icon {
    width: 40px; height: 40px; border-radius: 50%;
    background: var(--white);
    border: 3px solid var(--body-deep);
    box-shadow: 0 0 0 2px var(--icon-ring);
    display: flex; align-items: center; justify-content: center;
  }
  .benefit-icon svg { width: 26px; height: 26px; }
  .benefit-icon svg * { fill: var(--accent); stroke: var(--accent); }
  .supply-note {
    position: absolute; right: 28px; top: 250px;
    text-align: right; font-size: 11.5px; line-height: 1.35;
    color: var(--white);
  }
  .label--tl { left: 238px; top: 216px; }
  .label--tr { left: 630px; top: 228px; }
  .label--bl { left: 238px; top: 804px; }
  .label--br { left: 646px; top: 808px; }
</style>
</head>
<body>
<main class="canvas">

  <svg width="0" height="0" style="position:absolute">
    <defs>
      <symbol id="icon-joint" viewBox="0 0 26 26">
        <rect x="4" y="3" width="6" height="12" rx="3" stroke-width="0"/>
        <rect x="14" y="11" width="6" height="12" rx="3" stroke-width="0"/>
        <circle cx="12" cy="13" r="4" stroke-width="0"/>
      </symbol>
      <symbol id="icon-brain" viewBox="0 0 26 26">
        <ellipse cx="13" cy="12" rx="10" ry="7.5" stroke-width="0"/>
        <rect x="14" y="17" width="3" height="5" stroke-width="0"/>
      </symbol>
      <symbol id="icon-hair" viewBox="0 0 26 26">
        <rect x="3" y="18" width="20" height="4" stroke-width="0"/>
        <path d="M8 18 V6 M13 18 V4 M18 18 V7" stroke-width="1.6" fill="none"/>
      </symbol>
      <symbol id="icon-eye" viewBox="0 0 26 26">
        <path d="M13 3 C5 8 5 18 13 23 C21 18 21 8 13 3 Z" fill="none" stroke-width="1.8"/>
        <circle cx="13" cy="13" r="4" stroke-width="0"/>
      </symbol>
      <symbol id="icon-cells" viewBox="0 0 26 26">
        <ellipse cx="15" cy="8" rx="8" ry="4" stroke-width="0"/>
        <ellipse cx="11" cy="17" rx="8" ry="4" stroke-width="0"/>
      </symbol>
    </defs>
  </svg>

  <section class="label label--blue label--tl" aria-label="Blue label, black bottle">
    <div class="label__band label__band--top"></div>
    <div class="label__body" role="img" aria-label="Blue gradient with faint molecular structure pattern"></div>
    <div class="brand"><span class="brand__dot"></span><span class="brand__name">Volrex</span></div>
    <p class="brand__tagline">Powering Active Lives</p>
    <h2 class="product-title">Grape Seed Extract</h2>
    <p class="product-claim">Antioxidant Formula to Boost Immunity</p>
    <ul class="benefit-icons">
      <li class="benefit-icon"><svg aria-label="Joint health"><use href="#icon-joint"/></svg></li>
      <li class="benefit-icon"><svg aria-label="Brain health"><use href="#icon-brain"/></svg></li>
      <li class="benefit-icon"><svg aria-label="Hair health"><use href="#icon-hair"/></svg></li>
      <li class="benefit-icon"><svg aria-label="Eye health"><use href="#icon-eye"/></svg></li>
      <li class="benefit-icon"><svg aria-label="Blood health"><use href="#icon-cells"/></svg></li>
    </ul>
    <p class="supply-note">90 Day Supply<br>Dietary Supplement</p>
    <div class="label__band label__band--bottom"></div>
  </section>

  <section class="label label--blue label--tr" aria-label="Blue label, blue bottle">
    <div class="label__band label__band--top"></div>
    <div class="label__body" role="img" aria-label="Blue gradient with faint molecular structure pattern"></div>
    <div class="brand"><span class="brand__dot"></span><span class="brand__name">Volrex</span></div>
    <p class="brand__tagline">Powering Active Lives</p>
    <h2 class="product-title">Grape Seed Extract</h2>
    <p class="product-claim">Antioxidant Formula to Boost Immunity</p>
    <ul class="benefit-icons">
      <li class="benefit-icon"><svg aria-label="Joint health"><use href="#icon-joint"/></svg></li>
      <li class="benefit-icon"><svg aria-label="Brain health"><use href="#icon-brain"/></svg></li>
      <li class="benefit-icon"><svg aria-label="Hair health"><use href="#icon-hair"/></svg></li>
      <li class="benefit-icon"><svg aria-label="Eye health"><use href="#icon-eye"/></svg></li>
      <li class="benefit-icon"><svg aria-label="Blood health"><use href="#icon-cells"/></svg></li>
    </ul>
    <p class="supply-note">90 Day Supply<br>Dietary Supplement</p>
    <div class="label__band label__band--bottom"></div>
  </section>

  <section class="label label--red label--bl" aria-label="Red label, black bottle">
    <div class="label__band label__band--top"></div>
    <div class="label__body" role="img" aria-label="Red gradient with faint molecular structure pattern"></div>
    <div class="brand"><span class="brand__dot"></span><span class="brand__name">Volrex</span></div>
    <p class="brand__tagline">Powering Active Lives</p>
    <h2 class="product-title">Grape Seed Extract</h2>
    <p class="product-claim">Antioxidant Formula to Boost Immunity</p>
    <ul class="benefit-icons">
      <li class="benefit-icon"><svg aria-label="Joint health"><use href="#icon-joint"/></svg></li>
      <li class="benefit-icon"><svg aria-label="Brain health"><use href="#icon-brain"/></svg></li>
      <li class="benefit-icon"><svg aria-label="Hair health"><use href="#icon-hair"/></svg></li>
      <li class="benefit-icon"><svg aria-label="Eye health"><use href="#icon-eye"/></svg></li>
      <li class="benefit-icon"><svg aria-label="Blood health"><use href="#icon-cells"/></svg></li>
    </ul>
    <p class="supply-note">90 Day Supply<br>Dietary Supplement</p>
    <div class="label__band label__band--bottom"></div>
  </section>

  <section class="label label--red label--br" aria-label="Red label, blue bottle">
    <div class="label__band label__band--top"></div>
    <div class="label__body" role="img" aria-label="Red gradient with faint molecular structure pattern"></div>
    <div class="brand"><span class="brand__dot"></span><span class="brand__name">Volrex</span></div>
    <p class="brand__tagline">Powering Active Lives</p>
    <h2 class="product-title">Grape Seed Extract</h2>
    <p class="product-claim">Antioxidant Formula to Boost Immunity</p>
    <ul class="benefit-icons">
      <li class="benefit-icon"><svg aria-label="Joint health"><use href="#icon-joint"/></svg></li>
      <li class="benefit-icon"><svg aria-label="Brain health"><use href="#icon-brain"/></svg></li>
      <li class="benefit-icon"><svg aria-label="Hair health"><use href="#icon-hair"/></svg></li>
      <li class="benefit-icon"><svg aria-label="Eye health"><use href="#icon-eye"/></svg></li>
      <li class="benefit-icon"><svg aria-label="Blood health"><use href="#icon-cells"/></svg></li>
    </ul>
    <p class="supply-note">90 Day Supply<br>Dietary Supplement</p>
    <div class="label__band label__band--bottom"></div>
  </section>

</main>
</body>
</html>
```